Web Site Design For Real Estate Sales Project

The idea behind this project is pretty simple. I am putting my penthouse apartment up for sale and am trying to be creative in selling it.
Technically this will be pretty simple, it will be 3 pages but graphically this has to be as impressive as possible which is why I am trying Pixel Harbor.
The apartment is located in Barra Da Tijuca, Rio De Janeiro, Brazil. (This is where the 2016 Solstice Meet will be held)
I am looking for an index page and 2 sub-pages. I am open to all kinds of designs and navigation's but it has to make an impression quickly with a professional and enticing design. The index page should make it obvious that there is a penthouse apartment for sale in Barra Da Tijuca ( suburb of Rio De Janeiro). The first sub page is about the Condominium where the apartment is located, the second sub page is about the apartment itself.
Here is a more detailed description of what the 3 pages should be about.
Index Page
This is the landing page and should make it obvious that there is an apartment for sale in Barra Da Tijuca, Rio De Janeiro with the following attributes
251 SQ M
Duplex Penthouse
4 suites
Price R$ 2.200.000
Price per SQ M: R$ 8.764
First Sub-Page
This is about the Condominium which is called "Tranquil Cliff Suites" with the following bullets
*Family friendly and safe
*Direct access to the beach
*Many amenities like pool, football court, gym, sauna
There should be some photos of the condominium and a link to the site of the condominium ( www.tcsqv.com )
Second Sub-page
This is about the apartment. It should list in bullets the features of the apartment and then have a photo gallery of the view and various rooms. I have attached sample photos but will eventually have to use more photos.
Apartment Features
Price: R$ 2.220.000
251 m2 Duplex Penthouse
4 suites
maids room with bath
guest bathroom
living room
dinning room
Terrace with heated pool for year round use
Veranda
As mentioned above I am open to all designs and navigation so feel free to be creative. The important thing is catch peoples attention and get the message across in a few seconds, which is that there is an apartment for sale at this price with these features in this location. I will then use zintra clickreach and SEO to get people to the site.
Thanks
Men and Women from 30-60 years of age.
Apartment

```html
<!DOCTYPE html>
<html lang="en">
<head>
<meta charset="utf-8">
<title>Penthouse</title>
<link rel="stylesheet" href="https://fonts.googleapis.com/css2?family=PT+Sans+Narrow&family=Arvo:wght@400;700&family=PT+Sans&display=swap">
<style>
:root{
  --bg:#242424;
  --bg-stripe:#292929;
  --footer:#0f0f0f;
  --text-light:#f2f2f2;
  --text-muted:#c8c8c8;
  --btn-top:#ffffff;
  --btn-bottom:#bdbdbd;
  --btn-text:#222;
  --dark-chip:#0b0b0b;
  --divider:#6a6a6a;
  --overlay:rgba(110,110,110,.72);
}
*{box-sizing:border-box;margin:0;padding:0}
html,body{width:1200px;height:1128px;overflow:hidden}
body{
  background:var(--bg) repeating-linear-gradient(90deg,var(--bg) 0 22px,var(--bg-stripe) 22px 44px);
  font-family:"PT Sans",sans-serif;color:var(--text-light);position:relative;
}
.page{position:relative;width:1200px;height:1128px}
.brand{position:absolute;left:148px;top:28px;font:40px "PT Sans Narrow",sans-serif;color:#fff}
.call-icon{position:absolute;left:662px;top:20px}
.call-label{position:absolute;left:691px;top:18px;font:19px "PT Sans Narrow",sans-serif;color:var(--text-muted);white-space:nowrap}
.call-number{position:absolute;left:774px;top:17px;font:22px "PT Sans Narrow",sans-serif;letter-spacing:-0.3px;color:#fff;white-space:nowrap}
.search{position:absolute;left:897px;top:16px;width:152px;height:30px;background:#0d0d0d;border:2px solid #333;border-radius:4px;font-size:12px;color:#bbb;padding:6px 10px}
.search svg{position:absolute;right:8px;top:6px}
.nav{position:absolute;top:61px;left:662px;display:flex;gap:9px}
.nav-btn{height:32px;border-radius:3px;background:linear-gradient(var(--btn-top),var(--btn-bottom));border:1px solid #888;font:17px "PT Sans Narrow",sans-serif;color:var(--btn-text);display:flex;align-items:center;justify-content:center;white-space:nowrap}
.hero{position:absolute;left:150px;top:108px;width:897px;height:354px;box-shadow:0 16px 18px -8px #000;overflow:hidden}
.hero-photo{position:absolute;inset:0;background:linear-gradient(100deg,#6c7470 0%,#8c948c 30%,#d8cfb8 48%,#e4dcc6 55%,#8fb0bd 68%,#4a7f93 85%,#3d7188 100%)}
.arrow{position:absolute;width:54px;height:54px;border-radius:50%;background:rgba(15,15,15,.88);display:flex;align-items:center;justify-content:center}
.facts{position:absolute;left:543px;top:181px;width:258px;height:173px;background:var(--overlay);padding:12px 0 0 20px;font:24px/30.5px "PT Sans Narrow",sans-serif;color:#fff;white-space:nowrap}
.card{position:absolute;width:273px}
.card h2{font:700 16px/19px "Arvo",serif;color:#fff;height:38px;display:flex;align-items:flex-end;padding-bottom:4px}
.card-photo{width:273px;height:116px;box-shadow:0 3px 5px #000}
.card p{font-size:11.5px;letter-spacing:-0.1px;line-height:17px;color:#eee;margin-top:10px}
.read-more{display:inline-flex;align-items:center;gap:6px;margin-top:8px;height:26px;padding:0 7px;background:var(--dark-chip);border-radius:3px;font:700 14px "Arvo",serif;color:#fff}
.divider{position:absolute;left:153px;top:742px;width:896px;border-top:2px dashed var(--divider)}
.footer{position:absolute;left:0;top:1028px;width:1200px;height:100px;background:var(--footer)}
.follow{position:absolute;left:154px;top:23px;font-size:12px;color:var(--text-muted)}
.social{position:absolute;left:157px;top:52px;display:flex;gap:6px}
.social span{width:28px;height:28px;border-radius:50%;background:#f4f4f4;border:2px solid #9aa}
.footer-links{position:absolute;right:156px;top:23px;font-size:12px;color:var(--text-muted)}
.footer-links span{margin:0 5px}
.copyright{position:absolute;right:158px;top:55px;font-size:12px;color:var(--text-muted)}
</style>
</head>
<body>
<div class="page">
  <header>
    <div class="brand">Penthouse</div>
    <svg class="call-icon" width="22" height="24" viewBox="0 0 22 24"><path d="M3 3h4v18H3z" fill="#ddd"/><rect x="9" y="2" width="11" height="20" rx="2" fill="#ddd"/><g fill="#242424"><rect x="11" y="5" width="7" height="4"/><rect x="11" y="11" width="2" height="2"/><rect x="15" y="11" width="2" height="2"/><rect x="11" y="15" width="2" height="2"/><rect x="15" y="15" width="2" height="2"/></g></svg>
    <span class="call-label">Call Us Now</span>
    <span class="call-number">555.XXX.XXXX</span>
    <div class="search">Search
      <svg width="16" height="16" viewBox="0 0 16 16"><circle cx="6" cy="6" r="4.5" fill="none" stroke="#ddd" stroke-width="2"/><path d="M9.5 9.5l5 5" stroke="#ddd" stroke-width="3"/></svg>
    </div>
    <nav class="nav">
      <div class="nav-btn" style="width:99px">Home</div>
      <div class="nav-btn" style="width:164px">Tranquil Cliff Suites</div>
      <div class="nav-btn" style="width:108px">The Apartment</div>
    </nav>
  </header>

  <section class="hero">
    <div class="hero-photo" role="img" aria-label="Aerial view of beachfront towers along Barra da Tijuca beach"></div>
    <div class="arrow" style="left:36px;top:151px"><svg width="26" height="20" viewBox="0 0 26 20"><path d="M24 10H4M11 2L3 10l8 8" fill="none" stroke="#fff" stroke-width="3.5"/></svg></div>
    <div class="arrow" style="left:817px;top:153px"><svg width="26" height="20" viewBox="0 0 26 20"><path d="M2 10h20M15 2l8 8-8 8" fill="none" stroke="#fff" stroke-width="3.5"/></svg></div>
    <div class="facts">251 SQ M<br>Duplex Penthouse<br>4 suites<br>Price R$ 2.200.000<br>Price per SQ M: R$ 8.764</div>
  </section>

  <main>
    <article class="card" style="left:153px;top:486px">
      <h2>maids room with bath</h2>
      <div class="card-photo" role="img" aria-label="Rooftop pool seen from above" style="background:linear-gradient(135deg,#6e7a3a,#4fa7b0 45%,#8a8a4a 75%,#3c4a24)"></div>
      <p>Lorem Ipsum is simply dummy text of the printing and typesetting</p>
      <span class="read-more">read more <svg width="14" height="14" viewBox="0 0 14 14"><circle cx="7" cy="7" r="6.5" fill="#ddd"/><path d="M4 4l3 3-3 3zM7.5 4l3 3-3 3z" fill="#222"/></svg></span>
    </article>
    <article class="card" style="left:464px;top:486px">
      <h2>guest bathroom</h2>
      <div class="card-photo" role="img" aria-label="White guest bathroom with tub and basin" style="background:linear-gradient(180deg,#e8e6e2,#d8d6d2 55%,#f4f4f2 70%,#7a7a7a)"></div>
      <p>Lorem Ipsum is simply dummy text of the printing and typesetting</p>
      <span class="read-more">read more <svg width="14" height="14" viewBox="0 0 14 14"><circle cx="7" cy="7" r="6.5" fill="#ddd"/><path d="M4 4l3 3-3 3zM7.5 4l3 3-3 3z" fill="#222"/></svg></span>
    </article>
    <article class="card" style="left:773px;top:486px">
      <h2>living room</h2>
      <div class="card-photo" role="img" aria-label="Living room with artwork and wooden stair rail" style="background:linear-gradient(90deg,#b8a68a,#e6e2da 45%,#5a3020 65%,#dcdcd8)"></div>
      <p>Lorem Ipsum is simply dummy text of the printing and typesetting</p>
      <span class="read-more">read more <svg width="14" height="14" viewBox="0 0 14 14"><circle cx="7" cy="7" r="6.5" fill="#ddd"/><path d="M4 4l3 3-3 3zM7.5 4l3 3-3 3z" fill="#222"/></svg></span>
    </article>

    <div class="divider"></div>

    <article class="card" style="left:153px;top:771px">
      <h2>dinning room</h2>
      <div class="card-photo" role="img" aria-label="Dining room with table and dark wood floor" style="background:linear-gradient(90deg,#cfd6d8,#a89478 35%,#3a2618 60%,#e8e4de)"></div>
      <p>Lorem Ipsum is simply dummy text of the printing and typesetting</p>
      <span class="read-more">read more <svg width="14" height="14" viewBox="0 0 14 14"><circle cx="7" cy="7" r="6.5" fill="#ddd"/><path d="M4 4l3 3-3 3zM7.5 4l3 3-3 3z" fill="#222"/></svg></span>
    </article>
    <article class="card" style="left:464px;top:771px">
      <h2>Terrace with heated pool for year round use</h2>
      <div class="card-photo" role="img" aria-label="Terrace pool with white loungers" style="background:linear-gradient(180deg,#2e3236 0%,#3a3e42 60%,#2a8fd0 78%,#8a5044)"></div>
      <p>Lorem Ipsum is simply dummy text of the printing and typesetting</p>
      <span class="read-more">read more <svg width="14" height="14" viewBox="0 0 14 14"><circle cx="7" cy="7" r="6.5" fill="#ddd"/><path d="M4 4l3 3-3 3zM7.5 4l3 3-3 3z" fill="#222"/></svg></span>
    </article>
    <article class="card" style="left:773px;top:771px">
      <h2>Veranda</h2>
      <div class="card-photo" role="img" aria-label="Tiled veranda with railing and view of hills" style="background:linear-gradient(180deg,#7a8a6a,#4e3a2a 35%,#e6e6e4 60%,#cfcfcf)"></div>
      <p>Lorem Ipsum is simply dummy text of the printing and typesetting</p>
      <span class="read-more">read more <svg width="14" height="14" viewBox="0 0 14 14"><circle cx="7" cy="7" r="6.5" fill="#ddd"/><path d="M4 4l3 3-3 3zM7.5 4l3 3-3 3z" fill="#222"/></svg></span>
    </article>
  </main>

  <footer class="footer">
    <div class="follow">Follow Us on</div>
    <div class="social" aria-label="Social links"><span></span><span></span><span></span><span></span></div>
    <div class="footer-links">Home<span>|</span>Tranquil Cliff Suites<span>|</span>The Apartment</div>
    <div class="copyright">Copyrights @ 2013 All Rights Reserved</div>
  </footer>
</div>
</body>
</html>
```